Website design needed for gift based dropship website

I am building a dropshipping website that will create gift based merchandise and send it out to our clients customers for them. Our clients will sell products and when a customer buys from them, we create the item and send it out to the customer.

I am looking for a very similar website to stitchora.com - that website is doing a very similar thing to what i am doing but where the stitchora website is based around clothing, my website will be based around gifts. Another website that i like that is doing a similar thing to what i will do is pelvane.com

I require 2 pages to be made:
1) The home page
2) A landing page for a free product giveaway offer

1) THE HOME PAGE
The home page should be a merger of the two previously stated websites (www.pelvane.com and www.stitchora.com). The style fo the homepage should be based on the logo that is attached and the colour scheme should be similar but basic.

2) THE LANDING PAGE
The landing page will be giving away a free mobile phone cover. The page needs to have some mobile phone covers for different phones all with random designs on. The page should state that they can have any design that they want and they do not pay for the phone (they only pay for shipping).

Menu pages and text should be taken from the stitchora.com website.

Target Market(s)

18 - 40 year old males. People who like the idea of earning extra money in their spare time but aren't too sure how to do it. Semi-professional jobs.

Font styles to use
Serif
Sans Serif
Decorative
Script

Colors

Designer to choose colors to be used in the design.

Requirements
Must have
• A "how it works" image where the dropshipping process is explained to a visitor to the website (similar to the one on the stitchora "how it works page")
Nice to have
• Testimonial area on homepage
Should not have
• Homepage should not have:
• - "latest orders from" area
• - Video
• - Warehousing/fulfilment area
• - Integration area

```html
<!DOCTYPE html>
<html lang="en">
<head>
<meta charset="utf-8">
<title>Merrow Gifts – Personalised Gifts and Mementos</title>
<link href="https://fonts.googleapis.com/css2?family=Roboto+Condensed:wght@400;700&family=Jost:wght@400;500;600&display=swap" rel="stylesheet">
<style>
:root{
  --maroon:#6b1e2c;
  --maroon-deep:#4e1520;
  --ink:#150d10;
  --red:#e8382a;
  --text:#222;
  --muted:#777;
  --numeral:#d9d9d9;
  --paper:#fff;
  --panel:#f4f4f4;
}
*{box-sizing:border-box;margin:0;padding:0}
html,body{width:1200px;height:3000px;overflow:hidden;background:var(--paper)}
body{position:relative;font-family:"Jost",sans-serif;color:var(--text)}
.abs{position:absolute}
.display{font-family:"Roboto Condensed",sans-serif;font-weight:700}

/* hero */
.hero-photo-left{left:0;top:0;width:600px;height:632px;background:linear-gradient(135deg,#e2dfdf,#c9c3c3 55%,#b8403f 80%,#d9d5d5)}
.hero-photo-right{left:600px;top:0;width:600px;height:632px;background:linear-gradient(160deg,#7a2a37,var(--maroon) 50%,#5a1824)}
.brand{left:100px;top:0;width:190px;height:96px;background:var(--paper);display:flex;align-items:center;justify-content:center;gap:10px}
.brand-mark{width:22px;height:22px;border-radius:50%;background:var(--maroon)}
.brand-name{font-family:"Jost",sans-serif;font-weight:600;font-size:22px;color:var(--maroon);line-height:1}
.search-icon{left:1082px;top:20px}
.menu-btn{left:1134px;top:0;width:66px;height:64px;background:var(--paper);display:flex;align-items:center;justify-content:center}
.welcome{left:500px;top:318px;width:140px;transform:rotate(-90deg);transform-origin:center;font-family:"Jost",sans-serif;font-weight:600;font-size:11px;line-height:14px;color:var(--red);text-transform:uppercase;text-align:center}
.hero-card{left:530px;top:216px;width:482px;height:202px;border:2px solid var(--paper);background:rgba(150,110,120,.45)}
.hero-title{left:656px;top:250px;font-size:38px;color:var(--paper);letter-spacing:.5px}
.hero-sub{left:656px;top:302px;width:240px;font-size:12px;line-height:16px;color:var(--paper)}
.hero-btn{left:656px;top:352px;width:130px;height:36px;background:var(--paper);font-size:11px;font-weight:500;display:flex;align-items:center;justify-content:center;color:var(--text)}
.scroll-mouse{left:614px;top:566px}

/* section numbering */
.numeral{font-family:"Roboto Condensed",sans-serif;font-weight:700;color:var(--numeral);line-height:1}
.section-title{font-family:"Roboto Condensed",sans-serif;font-weight:700;color:var(--text);line-height:1}

/* how it works */
.step{width:190px;height:204px;border:3px dashed var(--maroon);text-align:center;padding-top:38px}
.step-title{font-size:19px;font-weight:500;line-height:22px;color:var(--text)}
.step-text{font-size:11px;line-height:17px;color:var(--text);margin:10px auto 0;width:136px}
.step-btn{position:absolute;left:34px;top:136px;width:118px;height:30px;background:var(--red);color:var(--paper);font-size:11px;font-weight:500;display:flex;align-items:center;justify-content:center}

/* products */
.lede{font-size:12px;font-weight:600;color:var(--text)}
.body-copy{font-size:11px;line-height:16px;color:var(--muted)}
.read-more{font-size:11px;font-weight:500;color:var(--text);display:flex;align-items:center;gap:8px}
.tile{background:#ccc}
.tile-gifts{left:424px;top:1150px;width:242px;height:172px;background:linear-gradient(135deg,#f0eeee,#c9302f 45%,#3a6aa8 75%,#e8e4e4)}
.tile-hands{left:424px;top:1322px;width:242px;height:168px;background:linear-gradient(135deg,#7fcfc6,#e0a63b 50%,#c4342c 70%,#86d0c8)}
.tile-woman{left:666px;top:1150px;width:214px;height:340px;background:linear-gradient(180deg,#d8d4d4,#c79a7a 35%,#b62d2f 60%,#c8c3c3)}
.tile-offer{left:880px;top:1150px;width:320px;height:170px;background:var(--red);padding:26px 30px;color:var(--paper)}
.tile-offer h3{font-size:12px;font-weight:600;line-height:16px}
.tile-offer p{font-size:10px;line-height:14px;margin-top:10px;opacity:.9}
.tile-offer .read-more{color:var(--paper);margin-top:14px;font-size:10px}
.tile-gift-hands{left:880px;top:1320px;width:320px;height:170px;background:linear-gradient(135deg,#cc8f6c,#f3f0ee 50%,#c7352e 65%,#d7a88a)}

/* difference + signup */
.band-left{left:0;top:1582px;width:600px;height:530px;background:linear-gradient(150deg,#7a2b38,var(--maroon) 55%,#561824)}
.band-right{left:600px;top:1582px;width:600px;height:530px;background:linear-gradient(150deg,#241418,var(--ink) 60%,#0b0708)}
.diff-card{left:160px;top:1664px;width:482px;height:366px;border:2px solid var(--paper);background:rgba(170,130,140,.4)}
.diff-num{left:192px;top:1700px;font-size:80px;color:rgba(255,255,255,.35)}
.diff-title{left:230px;top:1736px;font-family:"Jost",sans-serif;font-weight:500;font-size:28px;color:var(--paper);line-height:1}
.diff-item h4{font-size:13px;font-weight:600;color:var(--paper)}
.diff-item p{font-size:11px;line-height:16px;color:var(--paper);opacity:.9;margin-top:8px;width:300px}
.signup-num{left:676px;top:1676px;font-size:80px;color:rgba(255,255,255,.2)}
.signup-title{left:732px;top:1696px;font-family:"Jost",sans-serif;font-weight:500;font-size:28px;line-height:34px;color:var(--paper)}
.signup-title em{font-style:normal;color:var(--red)}
.field{left:732px;width:306px;height:30px;border:1px solid rgba(255,255,255,.7);font-size:10px;color:var(--paper);padding:0 10px;display:flex;align-items:center}
.signup-btn{left:732px;top:1950px;width:90px;height:30px;background:var(--red);color:var(--paper);font-size:11px;font-weight:500;display:flex;align-items:center;justify-content:center}

/* testimonials */
.meta{font-size:10px;font-weight:500;color:var(--text);display:flex;gap:28px}
.dash{width:14px;height:2px;background:var(--red)}
.quote-head{font-size:10px;font-weight:600;color:var(--text);text-transform:uppercase}
.testi-photo{left:612px;top:2204px;width:400px;height:232px;background:linear-gradient(180deg,#d9d6d6,#c59a7c 35%,#b82c2f 65%,#d2cece)}
.testi-tab{left:600px;top:2400px;width:112px;height:36px;background:var(--paper);justify-content:center}
.testi-card{top:2502px;width:258px;height:120px;background:var(--panel);padding:26px 30px}
.testi-card .dash{margin:10px 0 16px}
.testi-card.active{background:var(--red)}
.testi-card.active .meta,.testi-card.active .quote-head{color:var(--paper)}
.testi-card.active .dash{background:var(--paper)}

/* footer */
.rule{left:160px;top:2706px;width:880px;height:1px;background:#e6e6e6}
.foot-nav{left:0;top:2760px;width:1200px;display:flex;justify-content:center;gap:8px}
.foot-nav span{border:1px solid #ccc;font-size:10px;color:var(--muted);padding:5px 12px}
.contact{width:330px;display:flex;gap:14px}
.contact p{font-size:10px;line-height:18px;color:var(--red)}
.phone{font-size:10px;color:var(--text);display:flex;align-items:center;gap:10px}
.copyright{left:0;top:2958px;width:1200px;text-align:center;font-size:10px;color:var(--muted)}
</style>
</head>
<body>

<!-- Hero -->
<div class="abs hero-photo-left" role="img" aria-label="Smiling woman in a red patterned sweater holding a wrapped gift"></div>
<div class="abs hero-photo-right" role="img" aria-label="Dark maroon toned photo of hands holding a gift"></div>
<div class="abs brand"><span class="brand-mark"></span><span class="brand-name">Merrow Gifts</span></div>
<svg class="abs search-icon" width="24" height="24" viewBox="0 0 24 24" aria-hidden="true"><circle cx="10" cy="10" r="6" fill="none" stroke="#fff" stroke-width="2.4"/><line x1="14.5" y1="14.5" x2="20" y2="20" stroke="#fff" stroke-width="2.6" stroke-linecap="round"/></svg>
<div class="abs menu-btn"><svg width="22" height="16" viewBox="0 0 22 16" aria-hidden="true"><rect y="0" width="22" height="2.4" fill="#3d6fb6"/><rect y="6.8" width="22" height="2.4" fill="#3d6fb6"/><rect y="13.6" width="22" height="2.4" fill="#3d6fb6"/></svg></div>
<div class="abs hero-card"></div>
<div class="abs welcome">Welcome to the<br>Merrow Gifts</div>
<h1 class="abs display hero-title">SELL GIFT ONLINE</h1>
<p class="abs hero-sub">If you want to sell your designs in an online store or marketplace</p>
<div class="abs hero-btn">Connect Your Shop</div>
<svg class="abs scroll-mouse" width="28" height="46" viewBox="0 0 28 46" aria-hidden="true"><rect x="2" y="2" width="24" height="42" rx="12" fill="none" stroke="#fff" stroke-width="2"/><rect x="12.5" y="10" width="3" height="8" rx="1.5" fill="#fff"/></svg>

<!-- How it works -->
<div class="abs numeral" style="left:460px;top:692px;font-size:92px">01</div>
<h2 class="abs section-title" style="left:494px;top:718px;font-size:38px">HOW IT WORKS</h2>

<div class="abs step" style="left:162px;top:818px">
  <div class="step-title">Gerry</div>
  <p class="step-text">Garry Buys Something At our Store</p>
  <div class="step-btn">Step One</div>
</div>
<div class="abs step" style="left:390px;top:818px">
  <div class="step-title">Your Store</div>
  <p class="step-text">Order Get Sent Automatically To Merrow Gifts</p>
  <div class="step-btn">Step Two</div>
</div>
<div class="abs step" style="left:618px;top:818px">
  <div class="step-title">Merrow Gift</div>
  <p class="step-text">Product Get Made</p>
  <div class="step-btn">Step Three</div>
</div>
<div class="abs step" style="left:846px;top:818px;padding-top:26px">
  <div class="step-title">Your Product Factory</div>
  <p class="step-text" style="margin-top:6px">Your Brands All Over It!</p>
  <div class="step-btn">Step Four</div>
</div>

<!-- Products -->
<div class="abs numeral" style="left:42px;top:1150px;font-size:92px">02</div>
<h2 class="abs section-title" style="left:70px;top:1176px;font-size:42px">OUR PRODUCTS</h2>
<p class="abs lede" style="left:44px;top:1252px">Printed and shipped on demand, under your brand!</p>
<p class="abs body-copy" style="left:44px;top:1282px;width:340px">Lorem ipsum dolor sit amet, consectetur adipiscing elit, sed do eiusmod tempor incididunt ut labore et dolore magna aliqua. Ut enim ad minim veniam, quis nostrud exercitation ullamco laboris nisi ut aliquip ex ea commodo consequat.</p>
<p class="abs body-copy" style="left:44px;top:1364px;width:340px">Duis aute irure dolor in reprehenderit in voluptate velit esse cillum dolore eu fugiat nulla pariatur. Excepteur sint occaecat cupidatat non proident, sunt in culpa qui officia deserunt mollit anim id est laborum.</p>
<div class="abs read-more" style="left:44px;top:1446px"><svg width="14" height="8" viewBox="0 0 14 8" aria-hidden="true"><path d="M0 4h12M9 1l3 3-3 3" fill="none" stroke="#222" stroke-width="1.4"/></svg>Read More</div>

<div class="abs tile-gifts" role="img" aria-label="Pile of colourful wrapped gift boxes"></div>
<div class="abs tile-hands" role="img" aria-label="Hands passing a gold gift box with red ribbon on teal background"></div>
<div class="abs tile-woman" role="img" aria-label="Woman in red patterned sweater holding a gift"></div>
<div class="abs tile-offer">
  <h3>Lorem ipsum dolor sit amet, consectetur adipiscing elit, sed do eiusmod tempor</h3>
  <p>Lorem ipsum dolor sit amet, consectetur adipiscing elit...</p>
  <div class="read-more"><svg width="14" height="8" viewBox="0 0 14 8" aria-hidden="true"><path d="M0 4h12M9 1l3 3-3 3" fill="none" stroke="#fff" stroke-width="1.4"/></svg>Read More</div>
</div>
<div class="abs tile-gift-hands" role="img" aria-label="Open hands holding a small white gift with red ribbon"></div>

<!-- Difference + sign up -->
<div class="abs band-left" role="img" aria-label="Maroon toned photo of a person"></div>
<div class="abs band-right" role="img" aria-label="Dark photo of a person at work"></div>
<div class="abs diff-card"></div>
<div class="abs numeral diff-num">03</div>
<h2 class="abs diff-title">WHAT MAKES US DIFFERENT</h2>
<div class="abs diff-item" style="left:234px;top:1798px">
  <h4>Three fulfillment locations</h4>
  <p>We're located on both sides of the big pond to bring you closer to your customers</p>
</div>
<div class="abs diff-item" style="left:234px;top:1894px">
  <h4>No minimums</h4>
  <p>We print everything on demand so you can order as much as you need and you don't have to keep an inventory</p>
</div>
<div class="abs read-more" style="left:234px;top:1980px;color:#fff;font-size:10px">Read More <svg width="14" height="8" viewBox="0 0 14 8" aria-hidden="true"><path d="M0 4h12M9 1l3 3-3 3" fill="none" stroke="#fff" stroke-width="1.4"/></svg></div>

<div class="abs numeral signup-num">04</div>
<h2 class="abs signup-title">CREATE YOUR<br>MERROW GIFT<br>ACCOUNT FOR <em>FREE</em></h2>
<div class="abs field" style="top:1828px">Name</div>
<div class="abs field" style="top:1866px">Email</div>
<div class="abs field" style="top:1904px">Password</div>
<div class="abs signup-btn">Sign Up</div>

<!-- Testimonials -->
<div class="abs numeral" style="left:158px;top:2194px;font-size:84px">05</div>
<h2 class="abs section-title" style="left:190px;top:2236px;font-size:19px">TESTIMONIALS</h2>
<div class="abs meta" style="left:190px;top:2298px"><span>Monday, Jun 4, 2018</span><span>John Smith</span></div>
<div class="abs dash" style="left:190px;top:2320px"></div>
<p class="abs quote-head" style="left:190px;top:2350px">Lorem ipsum dolor sit amet consectetor</p>
<p class="abs body-copy" style="left:190px;top:2372px;width:340px">Lorem ipsum dolor sit amet, consectetur adipiscing elit, sed do eiusmod tempor incididunt ut labore et dolore magna aliqua. Ut enim ad minim veniam, quis nostrud exercitation ullamco laboris</p>
<div class="abs testi-photo" role="img" aria-label="Smiling woman in red patterned sweater holding a gift"></div>
<div class="abs read-more testi-tab"><svg width="14" height="8" viewBox="0 0 14 8" aria-hidden="true"><path d="M0 4h12M9 1l3 3-3 3" fill="none" stroke="#222" stroke-width="1.4"/></svg>Read More</div>

<div class="abs testi-card" style="left:188px">
  <div class="meta"><span>Monday, Jun 4, 2018</span><span>John Smith</span></div>
  <div class="dash"></div>
  <p class="quote-head">Dolor sit amet consecte</p>
</div>
<div class="abs testi-card active" style="left:470px">
  <div class="meta"><span>Monday, Jun 4, 2018</span><span>John Smith</span></div>
  <div class="dash"></div>
  <p class="quote-head">Contetor lorem sit amet</p>
</div>
<div class="abs testi-card" style="left:754px">
  <div class="meta"><span>Monday, Jun 4, 2018</span><span>John Smith</span></div>
  <div class="dash"></div>
  <p class="quote-head">Lorem ipsum dolor sit amet</p>
</div>

<!-- Footer -->
<div class="abs rule"></div>
<nav class="abs foot-nav">
  <span>Products &amp; Pricing</span><span>How it Works</span><span>Mockup generator</span><span>Shipping</span><span>Resources</span><span>FAQ</span><span>Blogs</span>
</nav>
<div class="abs contact" style="left:244px;top:2830px">
  <svg width="14" height="18" viewBox="0 0 14 18" aria-hidden="true"><path d="M7 0a7 7 0 0 1 7 7c0 5-7 11-7 11S0 12 0 7a7 7 0 0 1 7-7z" fill="#e8382a"/><circle cx="7" cy="7" r="2.6" fill="#fff"/></svg>
  <p>Lorem ipsum dolor sit amet, consectetur adipiscing elit, sed do eiusmod tempor incididunt ut labore et dolore magna aliqua.</p>
</div>
<div class="abs contact" style="left:652px;top:2830px">
  <svg width="14" height="18" viewBox="0 0 14 18" aria-hidden="true"><path d="M7 0a7 7 0 0 1 7 7c0 5-7 11-7 11S0 12 0 7a7 7 0 0 1 7-7z" fill="#e8382a"/><circle cx="7" cy="7" r="2.6" fill="#fff"/></svg>
  <p>Lorem ipsum dolor sit amet, consectetur adipiscing elit, sed do eiusmod tempor incididunt ut labore et dolore magna aliqua.</p>
</div>
<div class="abs phone" style="left:244px;top:2904px"><svg width="14" height="14" viewBox="0 0 14 14" aria-hidden="true"><path d="M3 1l2 3-1.4 1.6a8 8 0 0 0 4.8 4.8L10 9l3 2-1.2 2C6 13 1 8 1 2.2z" fill="#555"/></svg>01 23 456 789</div>
<div class="abs phone" style="left:652px;top:2904px"><svg width="14" height="14" viewBox="0 0 14 14" aria-hidden="true"><path d="M3 1l2 3-1.4 1.6a8 8 0 0 0 4.8 4.8L10 9l3 2-1.2 2C6 13 1 8 1 2.2z" fill="#555"/></svg>01 23 456 789</div>
<p class="abs copyright">© Copyright 2018 Merrow Gifts, all Rights Reserved.</p>

</body>
</html>
```